Tolbek cards

I want a simple business card that pops.
Logo on one side.
On side two i want.
"Are you thinking about a new building on your property, or renovating an existing structure? Contact".....
Owners Name: Dale Whitacre
Owners Phone number: 610-555-0187
Address:4076 Copper Ridge RD, Alder Springs, PA 17000
Committed to Quality, Service, and Integrity

```html
<!DOCTYPE html>
<html lang="en">
<head>
<meta charset="utf-8">
<title>Tolbek Builders – Business Cards</title>
<link href="https://fonts.googleapis.com/css2?family=Archivo:ital,wght@0,400;0,700;0,800;1,600&display=swap" rel="stylesheet">
<style>
  :root {
    --backdrop: #5b5b5b;
    --paper: #ffffff;
    --espresso: #422d1d;
    --bronze-light: #9e8769;
    --bronze-dark: #7a5f46;
    --ink: #4b3424;
    --on-dark: #ffffff;
  }
  * { margin: 0; padding: 0; box-sizing: border-box; }
  html, body {
    width: 1200px; height: 1200px; overflow: hidden;
    background: var(--backdrop);
    font-family: "Archivo", Arial, sans-serif;
  }
  .card {
    position: absolute;
    width: 690px; height: 394px;
    left: 263px;
    background: var(--paper);
    overflow: hidden;
  }
  .card--contact { top: 158px; }
  .card--brand { top: 652px; }
  .card__shapes { position: absolute; inset: 0; width: 100%; height: 100%; }
  .pitch {
    position: absolute; right: 23px; top: 36px;
    text-align: right;
    font-style: italic; font-weight: 600;
    font-size: 18.5px; line-height: 24px;
    color: var(--ink);
  }
  .wordmark {
    position: absolute;
    display: flex; align-items: center; gap: 14px;
    color: var(--espresso);
    font-weight: 800;
  }
  .wordmark__square { background: var(--espresso); flex: none; }
  .wordmark__name { display: flex; flex-direction: column; line-height: 1; }
  .card--contact .wordmark { right: 23px; top: 152px; }
  .card--contact .wordmark__square { width: 56px; height: 56px; }
  .card--contact .wordmark__title { font-size: 52px; letter-spacing: 0.5px; }
  .card--contact .wordmark__sub { font-size: 17px; letter-spacing: 1.5px; margin-top: 6px; }
  .contact {
    position: absolute; left: 36px; top: 246px;
    color: var(--on-dark); font-size: 15px; line-height: 21px;
  }
  .contact__phone { display: flex; align-items: center; gap: 10px; margin-bottom: 9px; }
  .contact__phone svg { width: 14px; height: 14px; fill: var(--on-dark); }
  .owner {
    position: absolute; left: 36px; top: 348px;
    color: var(--on-dark); font-weight: 700; font-size: 27px; letter-spacing: 0.5px;
  }
  .motto {
    position: absolute; right: 23px; top: 288px;
    color: var(--on-dark); font-size: 16.5px;
  }
  .card--brand .wordmark {
    left: 0; right: 0; top: 110px;
    flex-direction: column; gap: 18px;
  }
  .card--brand .wordmark__square { width: 70px; height: 70px; }
  .card--brand .wordmark__name { align-items: center; }
  .card--brand .wordmark__title { font-size: 72px; letter-spacing: 1px; }
  .card--brand .wordmark__sub { font-size: 22px; letter-spacing: 2px; margin-top: 6px; }
</style>
</head>
<body>
  <section class="card card--contact" aria-label="Business card, contact side">
    <svg class="card__shapes" viewBox="0 0 690 394" aria-hidden="true">
      <defs>
        <linearGradient id="bronzeSheen" x1="0" y1="0" x2="1" y2="1">
          <stop offset="0" stop-color="var(--bronze-light)"/>
          <stop offset="1" stop-color="var(--bronze-dark)"/>
        </linearGradient>
      </defs>
      <polygon points="0,0 16,0 215,230 0,230" fill="var(--espresso)"/>
      <path d="M0,230 H230 Q238,230 243,237 L321,334 H0 Z" fill="url(#bronzeSheen)"/>
      <polygon points="265,265 690,265 690,334 321,334" fill="var(--espresso)"/>
      <polygon points="0,334 306,334 357,394 0,394" fill="var(--espresso)"/>
    </svg>
    <p class="pitch">Are you thinking about a new building on your property,<br>or renovating an existing structure?</p>
    <div class="wordmark">
      <span class="wordmark__square"></span>
      <span class="wordmark__name"><span class="wordmark__title">TOLBEK</span><span class="wordmark__sub">BUILDERS LLC</span></span>
    </div>
    <div class="contact">
      <p class="contact__phone">
        <svg viewBox="0 0 24 24" aria-hidden="true"><path d="M6.6 10.8a15.1 15.1 0 0 0 6.6 6.6l2.2-2.2c.3-.3.7-.4 1-.2 1.1.4 2.3.6 3.6.6.6 0 1 .4 1 1V20c0 .6-.4 1-1 1A17 17 0 0 1 3 4c0-.6.4-1 1-1h3.5c.6 0 1 .4 1 1 0 1.3.2 2.5.6 3.6.1.3 0 .7-.2 1z"/></svg>
        610-555-0187
      </p>
      <p>4076 Copper Ridge RD<br>Alder Springs, PA 17000</p>
    </div>
    <p class="motto">Committed to Quality, Service, and Integrity</p>
    <p class="owner">DALE WHITACRE</p>
  </section>

  <section class="card card--brand" aria-label="Business card, brand side">
    <svg class="card__shapes" viewBox="0 0 692 394" aria-hidden="true">
      <defs>
        <linearGradient id="bronzeBand" x1="0" y1="0" x2="1" y2="0">
          <stop offset="0" stop-color="var(--bronze-dark)"/>
          <stop offset="0.5" stop-color="var(--bronze-light)"/>
          <stop offset="1" stop-color="var(--bronze-dark)"/>
        </linearGradient>
      </defs>
      <polygon points="0,324 344,324 374,361 0,361" fill="url(#bronzeBand)"/>
      <polygon points="357,336 692,336 692,361 374,361" fill="var(--espresso)"/>
    </svg>
    <div class="wordmark">
      <span class="wordmark__square"></span>
      <span class="wordmark__name"><span class="wordmark__title">TOLBEK</span><span class="wordmark__sub">BUILDERS LLC</span></span>
    </div>
  </section>
</body>
</html>
```